Business Card Design

Company is a Commercial Building Company specialising in New Construction and existing refurbishments

Industry/Entity Type

Business

Contact Information for Business Card

Liam Porter
Construction Manager
E Liam@marshbuilding.com.au
M 0400 213 594
Mail 14 Tarrant Rise Tidewater WA 6219

```html
<!DOCTYPE html>
<html lang="en">
<head>
<meta charset="utf-8">
<title>Marsh Building &amp; Construction — Business Card</title>
<link href="https://fonts.googleapis.com/css2?family=Roboto:wght@300;400;700&display=swap" rel="stylesheet">
<style>
  :root {
    --stage: #3a3c40;
    --card: #fbfdfd;
    --ink: #1f2433;
    --brand: #2a3450;
    --cyan: #1ab8d8;
    --orange: #f08a1e;
    --orange-deep: #d9740f;
    --faint: #e8eef3;
  }
  * { box-sizing: border-box; margin: 0; padding: 0; }
  html, body { width: 1200px; height: 960px; overflow: hidden; }
  body {
    background: var(--stage);
    font-family: "Roboto", Arial, sans-serif;
    position: relative;
  }
  .card {
    position: absolute;
    width: 560px;
    height: 320px;
    background: var(--card);
    overflow: hidden;
    box-shadow: 0 14px 30px rgba(0,0,0,.45);
  }
  .card--back { left: 70px; top: 110px; }
  .card--front { left: 570px; top: 530px; }

  .wordmark {
    position: absolute;
    color: var(--brand);
    font-weight: 700;
    text-transform: uppercase;
    line-height: 1.05;
    letter-spacing: .5px;
  }
  .card--back .wordmark { right: 48px; top: 44px; font-size: 24px; }
  .card--front .wordmark { left: 34px; top: 36px; font-size: 22px; }
  .wordmark small { display: block; font-size: .72em; letter-spacing: 1px; }

  .back-faint {
    position: absolute;
    left: 40px; bottom: 28px;
    font-size: 84px;
    font-weight: 700;
    color: var(--faint);
    letter-spacing: 4px;
  }

  .contact {
    position: absolute;
    right: 26px; top: 30px;
    list-style: none;
    color: var(--ink);
    font-size: 14px;
    text-align: right;
  }
  .contact li {
    display: flex;
    justify-content: flex-end;
    align-items: center;
    gap: 10px;
    height: 22px;
  }
  .contact svg { width: 16px; height: 16px; flex: none; }

  .bands { position: absolute; left: 0; top: 0; width: 560px; height: 320px; }
  .name {
    position: absolute;
    left: 36px; bottom: 30px;
    color: #fff;
    font-size: 26px;
    font-weight: 300;
  }
  .role {
    position: absolute;
    right: 30px; bottom: 66px;
    color: #fff;
    font-size: 15px;
    font-weight: 300;
  }
</style>
</head>
<body>

<section class="card card--back">
  <div class="wordmark">Marsh Building<small>&amp; Construction</small></div>
  <div class="back-faint">MARSH</div>
</section>

<section class="card card--front">
  <div class="wordmark">Marsh Building<small>&amp; Construction</small></div>

  <ul class="contact">
    <li>0400 213 594
      <svg viewBox="0 0 16 16"><rect width="16" height="16" rx="3" fill="#f08a1e"/><rect x="5" y="3" width="6" height="10" rx="1" fill="#1f2433"/></svg>
    </li>
    <li>Liam@marshbuilding.com.au
      <svg viewBox="0 0 16 16"><rect width="16" height="16" rx="3" fill="#f08a1e"/><rect x="3" y="5" width="10" height="7" fill="#1f2433"/><path d="M3 5l5 4 5-4" stroke="#f08a1e" fill="none"/></svg>
    </li>
    <li>14 Tarrant Rise Tidewater WA 6219
      <svg viewBox="0 0 16 16"><rect width="16" height="16" rx="3" fill="#f08a1e"/><path d="M8 3a3.5 3.5 0 0 1 3.5 3.5C11.5 9 8 13 8 13S4.5 9 4.5 6.5A3.5 3.5 0 0 1 8 3z" fill="#1f2433"/><circle cx="8" cy="6.5" r="1.3" fill="#f08a1e"/></svg>
    </li>
  </ul>

  <svg class="bands" viewBox="0 0 560 320" aria-hidden="true">
    <polygon points="0,226 330,226 350,206 560,160 560,320 0,320" fill="var(--cyan)"/>
    <polygon points="0,232 336,232 356,212 380,212 372,232 0,240" fill="var(--card)"/>
    <polygon points="0,238 350,238 366,220 392,220 350,320 0,320" fill="var(--card)"/>
    <polygon points="0,242 352,242 368,224 388,224 348,320 0,320" fill="var(--orange)"/>
    <line x1="10" y1="308" x2="330" y2="308" stroke="var(--orange-deep)" stroke-width="2"/>
  </svg>

  <div class="name">Liam Porter</div>
  <div class="role">Construction Manager</div>
</section>

</body>
</html>
```